iPhone iOS 7 App For Managing Tasks/Photos for Internal Company Use

We need an app design that displays company objectives and task, and provides the interface for employees to complete a task by uploading a photo and adding comments.

Please see attached mock up sketches as a rough guideline

Final delivery of files must contain PSD, and all layers/objects sliced both is PSD and PNG files

Target Market(s)

This is a tool for internal employee use

Industry/Entity Type

It Company

Requirements
Must have
• Must include logo, and match the colour scheme
Use iPhone iOS 7 Style

```html
<!DOCTYPE html>
<html lang="en">
<head>
<meta charset="utf-8">
<title>Objectives – Select An Objective</title>
<link rel="stylesheet" href="https://fonts.googleapis.com/css2?family=Open+Sans:wght@400;600;700&display=swap">
<style>
  :root {
    --screen-bg: #a8bac5;
    --header-bg: #ffffff;
    --brand-teal: #4f7078;
    --ink: #3f4449;
    --ink-dark: #000000;
    --panel-top: #c9d6de;
    --panel-bottom: #b3c3cc;
    --panel-edge: #8a9aa3;
    --row-divider: #5d666c;
    --row-active-top: #8ea0a8;
    --row-active-mid: #728891;
    --nav-ring: #5a7b82;
    --nav-ring-dark: #46656c;
    --nav-icon: #8f8f8f;
    --nav-label: #4d6b73;
  }
  * { box-sizing: border-box; margin: 0; padding: 0; }
  html, body { width: 675px; height: 1200px; overflow: hidden; }
  body {
    position: relative;
    background: var(--screen-bg);
    font-family: "Open Sans", "Segoe UI", sans-serif;
    color: var(--ink);
  }

  .status-bar {
    position: absolute; left: 0; top: 0; width: 675px; height: 51px;
    display: flex; align-items: center; justify-content: space-between;
    padding: 0 12px 6px; font-size: 22px; color: var(--ink-dark);
  }
  .status-left { display: flex; align-items: center; gap: 8px; }
  .signal { display: flex; gap: 3px; }
  .signal i { width: 10px; height: 10px; border-radius: 50%; border: 1.5px solid #000; display: block; }
  .signal i.on { background: #000; }
  .status-time { position: absolute; left: 0; right: 0; text-align: center; font-weight: 600; pointer-events: none; }
  .status-right { display: flex; align-items: center; gap: 8px; }
  .battery { width: 42px; height: 19px; border: 2px solid #000; border-radius: 4px; padding: 2px; position: relative; }
  .battery::after { content: ""; position: absolute; right: -5px; top: 5px; width: 3px; height: 6px; background: #000; border-radius: 0 2px 2px 0; }
  .battery span { display: block; height: 100%; background: #000; border-radius: 1px; }

  .app-header {
    position: absolute; left: 0; top: 51px; width: 675px; height: 84px;
    background: var(--header-bg);
    box-shadow: 0 2px 4px rgba(0,0,0,0.18);
  }
  .brand-name {
    position: absolute; left: 224px; top: 22px;
    font-size: 30px; font-weight: 700; color: var(--brand-teal); line-height: 40px;
    white-space: nowrap;
  }
  .brand-mark {
    position: absolute; left: 96px; top: 22px;
    font-size: 30px; font-weight: 700; color: var(--brand-teal); line-height: 40px;
  }

  .objective-select {
    position: absolute; left: 137px; top: 323px; width: 439px; height: 82px;
    border: 1px solid var(--panel-edge); border-radius: 5px;
    background: linear-gradient(#dbe3e8, #c3d0d8 55%, #b9c7cf);
    box-shadow: 0 1px 2px rgba(0,0,0,0.15);
    display: flex; align-items: center; padding: 0 22px 0 27px;
  }
  .objective-select .select-label { flex: 1; margin-left: 18px; font-size: 26px; font-weight: 600; color: var(--ink); }

  .objective-list {
    position: absolute; left: 137px; top: 436px; width: 439px; height: 320px;
    list-style: none;
    border: 1px solid var(--panel-edge); border-radius: 5px;
    background: linear-gradient(var(--panel-top), var(--panel-bottom));
    box-shadow: 0 1px 2px rgba(0,0,0,0.15);
  }
  .list-pointer { position: absolute; right: 25px; top: -13px; }
  .objective-row {
    height: 80px; display: flex; align-items: center; padding-left: 84px;
    font-size: 26px; font-weight: 700; color: var(--ink);
    border-bottom: 2px solid var(--row-divider);
  }
  .objective-row:last-child { border-bottom: none; }
  .objective-row.is-active {
    background: linear-gradient(var(--row-active-top), var(--row-active-mid) 60%, #8499a1);
    color: #33393d;
  }

  .tab-bar { position: absolute; left: 0; top: 1045px; width: 675px; height: 155px; }
  .tab-labels { position: absolute; top: 1140px; left: 0; width: 675px; height: 40px; }
  .tab-label { position: absolute; font-size: 26px; font-weight: 600; color: var(--nav-label); transform: translateX(-50%); white-space: nowrap; }
</style>
</head>
<body>
  <div class="status-bar">
    <div class="status-left">
      <div class="signal"><i class="on"></i><i class="on"></i><i class="on"></i><i></i><i></i></div>
      <span>NORTHTEL</span>
      <svg width="24" height="18" viewBox="0 0 24 18" aria-hidden="true"><path d="M2 6a14 14 0 0 1 20 0M5.5 9.5a9 9 0 0 1 13 0M9 13a4 4 0 0 1 6 0" fill="none" stroke="#000" stroke-width="2.4" stroke-linecap="round"/><circle cx="12" cy="16" r="1.6"/></svg>
    </div>
    <div class="status-time">4:21 PM</div>
    <div class="status-right">
      <svg width="14" height="22" viewBox="0 0 14 22" aria-hidden="true"><path d="M2 6l10 10-5 5V1l5 5L2 16" fill="none" stroke="#000" stroke-width="1.6"/></svg>
      <span>100%</span>
      <div class="battery"><span></span></div>
    </div>
  </div>

  <header class="app-header">
    <span class="brand-mark">Tavrelo</span>
    <span class="brand-name">COMPANY NAME</span>
  </header>

  <div class="objective-select">
    <svg width="36" height="30" viewBox="0 0 36 30" aria-hidden="true">
      <circle cx="14" cy="15" r="12" fill="none" stroke="#4a4f55" stroke-width="3"/>
      <circle cx="14" cy="15" r="6" fill="none" stroke="#4a4f55" stroke-width="3"/>
      <path d="M14 15L34 9" stroke="#4a4f55" stroke-width="3"/>
      <path d="M30 6l5 3-4 4" fill="#4a4f55"/>
    </svg>
    <span class="select-label">Select An Objective</span>
    <svg width="22" height="14" viewBox="0 0 22 14" aria-hidden="true"><path d="M3 3l8 8 8-8" fill="none" stroke="#55595e" stroke-width="3.5"/></svg>
  </div>

  <ul class="objective-list">
    <svg class="list-pointer" width="26" height="14" viewBox="0 0 26 14" aria-hidden="true"><path d="M0 14L13 1l13 13" fill="#ccd8df" stroke="#8a9aa3" stroke-width="1"/></svg>
    <li class="objective-row">Objective 1</li>
    <li class="objective-row is-active">Objective 2</li>
    <li class="objective-row">Objective 3</li>
    <li class="objective-row">Objective 4</li>
  </ul>

  <svg class="tab-bar" viewBox="0 1045 675 155" aria-label="Tab bar">
    <defs>
      <radialGradient id="face" cx="0.4" cy="0.35" r="0.7">
        <stop offset="0" stop-color="#ffffff"/><stop offset="1" stop-color="#dcdcdc"/>
      </radialGradient>
    </defs>
    <path d="M102 1082 Q184 1100 265 1082 Q344 1100 423 1082 Q503 1100 583 1082 L583 1102 Q503 1088 423 1102 Q344 1088 265 1102 Q184 1088 102 1102 Z" fill="var(--nav-ring)"/>
    <g fill="var(--nav-ring)" stroke="var(--nav-ring-dark)" stroke-width="2">
      <circle cx="102" cy="1090" r="44"/><circle cx="265" cy="1090" r="44"/>
      <circle cx="423" cy="1090" r="44"/><circle cx="583" cy="1090" r="44"/>
    </g>
    <g fill="url(#face)">
      <circle cx="102" cy="1090" r="33"/><circle cx="265" cy="1090" r="33"/>
      <circle cx="423" cy="1090" r="33"/><circle cx="583" cy="1090" r="33"/>
    </g>
    <g fill="var(--nav-icon)">
      <path d="M83 1091l19-18 19 18h-5v16h-28v-16z"/>
      <rect x="97" y="1095" width="10" height="12" fill="#f3f3f3"/>
    </g>
    <g fill="none" stroke="var(--nav-icon)" stroke-width="4">
      <circle cx="261" cy="1092" r="15"/><circle cx="261" cy="1092" r="7"/>
      <path d="M261 1092l18-14"/>
    </g>
    <g fill="var(--nav-icon)">
      <path d="M407 1098l24-22 8 16-26 10z"/>
      <path d="M413 1100l4 12 6-2-3-12z"/>
      <path d="M441 1078a12 12 0 0 1 3 14" fill="none" stroke="var(--nav-icon)" stroke-width="2.5"/>
    </g>
    <g fill="var(--nav-icon)">
      <path d="M567 1072h18v6h-12v26h12v6h-18z"/>
      <path d="M573 1076l14 4v28l-14 4z"/>
      <path d="M589 1086h6v-6l10 10-10 10v-6h-6z"/>
    </g>
  </svg>
  <nav class="tab-labels">
    <span class="tab-label" style="left:100px">Home</span>
    <span class="tab-label" style="left:268px">Objectives</span>
    <span class="tab-label" style="left:417px">News</span>
    <span class="tab-label" style="left:580px">Log Out</span>
  </nav>
</body>
</html>
```